Create a memorable Stationary for Security Software Company

Velbrantix is the worldwide leader in securing the Internet. Making Internet communications and critical data secure, reliable and available everywhere has been and continues to be our ongoing vision. We are committed to staying focused on real customer needs and to developing new and innovative security solutions that redefine the security landscape.

Industry/Entity Type

Internet

Font styles to use
Serif
Sans Serif
Script

Colors
0792cd
33a6d7
85cae6

```html
<!DOCTYPE html>
<html lang="en">
<head>
<meta charset="utf-8">
<title>Velbrantix Business Card</title>
<link rel="stylesheet" href="https://fonts.googleapis.com/css2?family=Quicksand:wght@500;600;700&display=swap">
<style>
  :root {
    --bg: #2a2a2c;
    --card: #141518;
    --blue-deep: #0792cd;
    --blue: #33a6d7;
    --blue-light: #85cae6;
  }
  * { margin: 0; padding: 0; box-sizing: border-box; }
  html, body { width: 1200px; height: 1189px; overflow: hidden; }
  body {
    background: var(--bg);
    font-family: "Quicksand", sans-serif;
    position: relative;
  }
  .card {
    position: absolute;
    left: 145px;
    width: 910px;
    height: 520px;
    background: var(--card);
    border-radius: 30px;
    box-shadow: 0 20px 40px rgba(0,0,0,.45);
  }
  .card--front { top: 50px; }
  .card--back { top: 619px; }

  .brand {
    display: flex;
    align-items: center;
    gap: 18px;
    color: var(--blue);
    font-weight: 700;
  }
  .brand__mark {
    width: 62px; height: 62px;
    border-radius: 50%;
    background: var(--blue);
    flex: none;
  }

  .card--front .brand {
    position: absolute;
    left: 50%; top: 190px;
    transform: translateX(-50%);
    font-size: 64px;
  }
  .card--front .brand__mark { width: 78px; height: 78px; }
  .front__url {
    position: absolute;
    left: 0; right: 0; top: 360px;
    text-align: center;
    color: var(--blue-deep);
    font-size: 24px;
    font-weight: 600;
  }

  .card--back .brand {
    position: absolute;
    left: 70px; top: 130px;
    font-size: 52px;
  }
  .social {
    position: absolute;
    right: 60px; top: 50px;
    display: flex; gap: 16px;
  }
  .social__tile {
    width: 34px; height: 34px;
    border-radius: 4px;
    background: var(--blue-light);
  }
  .person {
    position: absolute;
    right: 60px; top: 210px;
    display: flex; align-items: flex-end; gap: 12px;
  }
  .person__name { color: var(--blue); font-size: 36px; font-weight: 700; line-height: 1; }
  .person__role { color: var(--blue-light); font-size: 22px; font-weight: 600; line-height: 1; }
  .divider {
    position: absolute;
    left: 70px; right: 300px; top: 262px;
    height: 2px;
    background: var(--blue-light);
  }
  .contact {
    position: absolute;
    left: 70px; top: 330px;
    list-style: none;
  }
  .contact__item {
    display: flex; align-items: center; gap: 16px;
    color: var(--blue-deep);
    font-size: 28px; font-weight: 600;
    height: 44px;
  }
  .contact__icon {
    width: 28px; height: 28px;
    border-radius: 4px;
    background: var(--blue-light);
    display: flex; align-items: center; justify-content: center;
  }
  .address {
    position: absolute;
    right: 60px; top: 300px;
    text-align: right;
    color: var(--blue-deep);
    font-size: 28px; font-weight: 600;
    line-height: 1.35;
    font-style: normal;
  }
</style>
</head>
<body>
  <section class="card card--front">
    <div class="brand"><span class="brand__mark"></span><span class="brand__name">Velbrantix</span></div>
    <p class="front__url">www.velbrantix.net</p>
  </section>

  <section class="card card--back">
    <div class="social">
      <span class="social__tile"></span>
      <span class="social__tile"></span>
    </div>
    <div class="brand"><span class="brand__mark"></span><span class="brand__name">Velbrantix</span></div>
    <div class="person">
      <span class="person__name">Employee Name</span>
      <span class="person__role">Principal</span>
    </div>
    <div class="divider"></div>
    <ul class="contact">
      <li class="contact__item">
        <span class="contact__icon">
          <svg width="16" height="20" viewBox="0 0 16 20"><rect x="2" y="1" width="12" height="18" rx="2" fill="none" stroke="#141518" stroke-width="2"/><rect x="5" y="4" width="6" height="5" fill="#141518"/></svg>
        </span>000 000 0000
      </li>
      <li class="contact__item">
        <span class="contact__icon">
          <svg width="20" height="14" viewBox="0 0 20 14"><rect x="1" y="1" width="18" height="12" fill="none" stroke="#141518" stroke-width="2"/><path d="M1 1 L10 8 L19 1" fill="none" stroke="#141518" stroke-width="2"/></svg>
        </span>hello@velbrantix.net
      </li>
      <li class="contact__item">
        <span class="contact__icon">
          <svg width="20" height="20" viewBox="0 0 20 20"><circle cx="10" cy="10" r="8" fill="none" stroke="#141518" stroke-width="2"/><path d="M2 10 H18 M10 2 C5 7 5 13 10 18 M10 2 C15 7 15 13 10 18" fill="none" stroke="#141518" stroke-width="1.5"/></svg>
        </span>www.velbrantix.net
      </li>
    </ul>
    <address class="address">0000 Your Address, 2nd Ste.<br>Northvale, Elmora 1234</address>
  </section>
</body>
</html>
```